Website Development for vaultmerrow.com.au

Build a new Wordpress/Responsive website for vaultmerrow.com.au

Target Market(s)

Compliance Managers, Risk Managers, Information Security and Cyber Security Professionals, Chief Data/Digital Officers, Chief Operating/Financial Officers, Business Continuity Professionals, Disaster Recovery Planners, Small Business Owners, Local/Federal Government entities

Industry/Entity Type

Data Service

Coding

Coded - Design and coding required

Number of Pages Required

5+ page

Font styles to use
Sans Serif

Colors

Designer to choose colors to be used in the design.

Requirements
Must have
• 1. Site Structure: Home Page plus the following chapter-pages for a) Services b) About c) Resources d) Blog e) Contact Us
• 2. Prefer site to built on wordpress and we can purchase a theme if needed (we currently use Kelp9 for other sites)
• 3. Blog needs to be wordpress based
• 4. We will host the site ourselves on our own servers
• 5. Responsive Design
Nice to have
• 1. Livechat capability/interface
• 2. Capability for marketing automation integration (such as hubspot, marketo, infusionsoft etc)
• 3. Capability for CRM integration (Salesforce)

```html
<!DOCTYPE html>
<html lang="en">
<head>
<meta charset="utf-8">
<title>Vaultmerrow | About</title>
<link href="https://fonts.googleapis.com/css2?family=Roboto:wght@300;400;500;700;900&display=swap" rel="stylesheet">
<style>
:root{
  --red:#d3202b;
  --red-dark:#a3121b;
  --red-deep:#7e0c13;
  --ink:#2b2b2b;
  --grey:#6d6d6d;
  --grey-light:#9a9a9a;
  --line:#e4e4e4;
  --footer:#5b5b5b;
  --footer-dark:#4a4a4a;
  --white:#ffffff;
  --page:#ffffff;
}
*{box-sizing:border-box;margin:0;padding:0}
html,body{width:1200px;height:3060px;overflow:hidden}
body{font-family:'Roboto',Arial,sans-serif;background:var(--page);color:var(--ink);position:relative}
a{color:inherit;text-decoration:none}

/* Header */
.site-header{position:absolute;left:0;top:0;width:1200px;height:128px;background:var(--white)}
.topbar{position:absolute;left:0;top:0;width:1200px;height:34px;border-bottom:1px solid var(--line);font-size:12px;color:var(--grey)}
.topbar .contact{position:absolute;left:300px;top:10px;display:flex;gap:28px}
.topbar .contact span{display:flex;align-items:center;gap:6px}
.topbar .follow{position:absolute;right:24px;top:7px;display:flex;align-items:center;gap:6px}
.topbar .follow i{display:block;width:18px;height:18px;border-radius:50%;background:var(--red)}
.brand{position:absolute;left:140px;top:58px;display:flex;align-items:center;gap:10px;font-size:34px;font-weight:900;color:var(--red);letter-spacing:-0.5px}
.brand .mark{width:30px;height:30px;border-radius:50%;background:var(--red)}
.main-nav{position:absolute;right:32px;top:66px;display:flex;gap:0}
.main-nav a{display:block;padding:12px 14px;font-size:13px;font-weight:500;color:var(--ink);text-transform:uppercase;border-top:3px solid transparent}
.main-nav a.active{color:var(--red);border-top-color:var(--red)}
.main-nav a+a{border-left:1px solid var(--line)}

/* Hero */
.hero{position:absolute;left:0;top:128px;width:1200px;height:400px;overflow:hidden}
.hero-visual{position:absolute;inset:0;background:linear-gradient(100deg,#5a0a10 0%,var(--red-dark) 35%,#c81d28 62%,#d92d33 80%,#9a1119 100%)}
.hero-copy{position:absolute;left:140px;top:64px;color:var(--white);text-transform:uppercase}
.hero-copy h1{font-size:42px;font-weight:300;line-height:1.2;letter-spacing:1px}
.hero-copy h1 strong{font-weight:700}
.hero-copy p{margin-top:10px;font-size:30px;font-weight:400;text-transform:none}
.hero-curve{position:absolute;left:0;bottom:0;width:1200px;height:80px}

/* Breadcrumb */
.breadcrumb{position:absolute;left:140px;top:544px;font-size:13px;color:var(--grey)}
.breadcrumb b{color:var(--red);font-weight:500}
.breadcrumb-rule{position:absolute;left:0;top:590px;width:1200px;height:1px;background:var(--line)}

/* About */
.section-title{position:absolute;left:0;width:1200px;text-align:center;font-size:38px;font-weight:700;text-transform:uppercase;letter-spacing:1px}
.section-title .name{color:var(--red);text-transform:none;font-weight:900}
.section-title .underline{display:block;width:60px;height:3px;background:var(--red);margin:14px auto 0}
.about-title{top:618px;color:var(--ink)}
.about-photo{position:absolute;left:140px;top:700px;width:440px;height:460px;background:linear-gradient(160deg,#e7e9ec 0%,#c9ced6 55%,#8c95a2 100%)}
.body-copy{font-size:13px;line-height:1.75;color:var(--grey)}
.body-copy p+p{margin-top:14px}
.body-copy .lead{color:var(--red);font-weight:700}
.about-text{position:absolute;left:620px;top:700px;width:440px}

/* Team */
.team{position:absolute;left:0;top:1200px;width:1200px;height:620px;background:linear-gradient(180deg,#b7141d 0%,var(--red) 50%,#b3121a 100%)}
.team .section-title{top:80px;color:var(--white)}
.team .section-title .underline{background:var(--white)}
.team .subtitle{position:absolute;left:0;top:150px;width:1200px;text-align:center;color:var(--white);font-size:22px;font-weight:300}
.cards{position:absolute;left:175px;top:185px;display:flex;gap:30px}
.card{width:190px;height:380px;background:var(--white);padding:8px;box-shadow:0 6px 14px rgba(0,0,0,.25)}
.card-inner{width:100%;height:100%;border:1px solid #f1b9bc;text-align:center;padding:10px}
.card-photo{width:152px;height:200px;margin:0 auto;background:linear-gradient(180deg,#d9dde3,#9aa3ae)}
.card h3{margin-top:22px;font-size:14px;font-weight:700;text-transform:uppercase;color:var(--ink)}
.card.active h3{color:var(--red)}
.card .role{margin-top:6px;font-size:11px;color:var(--grey-light)}
.card .socials{margin-top:14px;display:flex;justify-content:center;gap:8px}
.card .socials i{width:12px;height:12px;border-radius:50%;background:#bdbdbd}
.card .rule{width:40px;height:2px;background:var(--red);margin:16px auto 0}
.arrow{position:absolute;top:360px;width:28px;height:28px;border-radius:50%;background:var(--white)}
.arrow.prev{left:136px}
.arrow.next{left:1036px}

/* Support */
.support-text{position:absolute;left:140px;top:1900px;width:420px}
.support-text .cta{margin-top:16px;font-weight:700;color:var(--ink)}
.support-text .cta a{color:var(--red);font-weight:400}
.support-photo{position:absolute;left:600px;top:1890px;width:460px;height:450px;background:linear-gradient(150deg,#f0f1f2 0%,#c7cbd1 50%,#7a828d 100%)}

/* Get started */
.get-started{position:absolute;left:0;top:2420px;width:1200px;height:410px;background:linear-gradient(135deg,#c41a24 0%,var(--red) 50%,#a8121b 100%)}
.get-started .section-title{top:60px;color:var(--white)}
.get-started .section-title .underline{background:var(--white)}
.contact-form{position:absolute;left:320px;top:150px;width:560px}
.field-row{display:flex;gap:20px}
.field{flex:1;height:40px;border:1px solid rgba(255,255,255,.55);color:rgba(255,255,255,.85);font-size:12px;padding:12px 12px}
.field.message{margin-top:18px;height:90px}
.submit{display:block;width:110px;margin:22px auto 0;padding:11px 0;background:var(--ink);color:var(--white);font-size:13px;font-weight:500;text-align:center;border-radius:2px}
.chat-launcher{position:absolute;left:1030px;top:2792px;width:48px;height:48px;border-radius:50%;background:var(--white);box-shadow:0 3px 8px rgba(0,0,0,.3)}

/* Footer */
.site-footer{position:absolute;left:0;top:2830px;width:1200px;height:230px;background:var(--footer);color:var(--white)}
.footer-brand{position:absolute;left:0;top:40px;width:1200px;display:flex;justify-content:center;align-items:center;gap:10px;font-size:32px;font-weight:900}
.footer-brand .mark{width:28px;height:28px;border-radius:50%;background:var(--white)}
.footer-nav{position:absolute;left:0;top:118px;width:1200px;display:flex;justify-content:center;gap:66px;font-size:12px;text-transform:uppercase}
.footer-bottom{position:absolute;left:0;top:180px;width:1200px;height:50px;background:var(--footer-dark);font-size:11px;color:#d6d6d6}
.footer-bottom .copy{position:absolute;left:140px;top:19px}
.footer-bottom .legal{position:absolute;right:140px;top:19px}
</style>
</head>
<body>

<header class="site-header">
  <div class="topbar">
    <div class="contact">
      <span><svg width="11" height="11" viewBox="0 0 24 24"><path fill="#d3202b" d="M6.6 10.8a15 15 0 0 0 6.6 6.6l2.2-2.2a1 1 0 0 1 1-.25 11.4 11.4 0 0 0 3.6.57 1 1 0 0 1 1 1V20a1 1 0 0 1-1 1A17 17 0 0 1 3 4a1 1 0 0 1 1-1h3.5a1 1 0 0 1 1 1c0 1.25.2 2.45.57 3.57a1 1 0 0 1-.25 1z"/></svg>(03) 5550 1482</span>
      <span><svg width="12" height="10" viewBox="0 0 24 18"><rect x="1" y="1" width="22" height="16" fill="none" stroke="#d3202b" stroke-width="2"/><path d="M1 1l11 9 11-9" fill="none" stroke="#d3202b" stroke-width="2"/></svg>info@vaultmerrow.com.au</span>
    </div>
    <div class="follow">Follow Us on <i></i><i></i><i></i><i></i></div>
  </div>
  <a class="brand" href="#"><span class="mark"></span>Vaultmerrow</a>
  <nav class="main-nav">
    <a href="#">Home</a>
    <a href="#" class="active">About</a>
    <a href="#">Services</a>
    <a href="#">Resources</a>
    <a href="#">Blog</a>
    <a href="#">Contact Us</a>
  </nav>
</header>

<section class="hero">
  <div class="hero-visual" role="img" aria-label="Hand touching a glowing red digital globe of connected data icons"></div>
  <div class="hero-copy">
    <h1>Delivering <strong>Quality</strong><br>Services Through<br><strong>Innovation</strong></h1>
    <p>From Industry Experts</p>
  </div>
  <svg class="hero-curve" viewBox="0 0 1200 80" preserveAspectRatio="none"><path d="M0 80 L0 40 Q600 110 1200 20 L1200 80 Z" fill="#ffffff"/></svg>
</section>

<div class="breadcrumb">HOME &nbsp;&gt;&nbsp; <b>ABOUT</b></div>
<div class="breadcrumb-rule"></div>

<h2 class="section-title about-title">About <span class="name">Vaultmerrow</span><span class="underline"></span></h2>

<div class="about-photo" role="img" aria-label="Businessman in a suit working at a laptop in a bright office"></div>
<div class="about-text body-copy">
  <p><span class="lead">Vaultmerrow</span> is a trusted Australian partner for data protection, helping organisations keep critical information safe, available and compliant across every part of the business.</p>
  <p>Our team designs backup, recovery and continuity plans that suit the way you work, so a single failure never becomes a lasting crisis.</p>
  <p>We work with compliance and risk managers, security teams and business owners to map where data lives, test how it is guarded and set clear steps for restoring it fast. From small offices to government agencies, every plan is shaped around real threats, real budgets and the rules your sector must meet.</p>
</div>

<section class="team">
  <h2 class="section-title">Our Team<span class="underline"></span></h2>
  <p class="subtitle">Our Bestest Team Members.</p>
  <span class="arrow prev"></span>
  <span class="arrow next"></span>
  <div class="cards">
    <article class="card"><div class="card-inner">
      <div class="card-photo" role="img" aria-label="Portrait of a team member"></div>
      <h3>Marla Quint</h3><p class="role">Designation Here</p>
      <div class="socials"><i></i><i></i><i></i></div><div class="rule"></div>
    </div></article>
    <article class="card active"><div class="card-inner">
      <div class="card-photo" role="img" aria-label="Portrait of a team member"></div>
      <h3>Tessa Rowe</h3><p class="role">Designation Here</p>
      <div class="socials"><i></i><i></i><i></i></div><div class="rule"></div>
    </div></article>
    <article class="card"><div class="card-inner">
      <div class="card-photo" role="img" aria-label="Portrait of a team member"></div>
      <h3>Owen Pyke</h3><p class="role">Designation Here</p>
      <div class="socials"><i></i><i></i><i></i></div><div class="rule"></div>
    </div></article>
    <article class="card"><div class="card-inner">
      <div class="card-photo" role="img" aria-label="Portrait of a team member"></div>
      <h3>Ravi Holm</h3><p class="role">Designation Here</p>
      <div class="socials"><i></i><i></i><i></i></div><div class="rule"></div>
    </div></article>
  </div>
</section>

<div class="support-text body-copy">
  <p>Downtime costs more than money. It costs trust, time and the confidence of the people who rely on your services every day.</p>
  <p>Our specialists review your systems, find the weak points and build a recovery path you can test and trust.</p>
  <p>Whether you need cloud backup, on-site replication, cyber incident response or a full continuity program, we bring practical advice and steady support. Each engagement starts with a clear review of your current setup and ends with documented plans, trained staff and regular checks that keep your protection current as your business grows.</p>
  <p class="cta">Get the support you need now. <a href="#">Contact our 24/7 support line to get started.</a></p>
</div>
<div class="support-photo" role="img" aria-label="Smiling woman with glasses working on a laptop"></div>

<section class="get-started">
  <h2 class="section-title">Let's Get Started<span class="underline"></span></h2>
  <form class="contact-form">
    <div class="field-row">
      <div class="field">Your Name</div>
      <div class="field">Your Email</div>
    </div>
    <div class="field message">Your Message</div>
    <span class="submit">Submit</span>
  </form>
</section>
<span class="chat-launcher"><svg width="48" height="48" viewBox="0 0 48 48"><path d="M14 16h20a2 2 0 0 1 2 2v11a2 2 0 0 1-2 2H22l-6 5v-5h-2a2 2 0 0 1-2-2V18a2 2 0 0 1 2-2z" fill="#d3202b"/></svg></span>

<footer class="site-footer">
  <div class="footer-brand"><span class="mark"></span>Vaultmerrow</div>
  <nav class="footer-nav">
    <a href="#">Home</a><a href="#">About</a><a href="#">Services</a><a href="#">Resources</a><a href="#">Blog</a><a href="#">Contact Us</a>
  </nav>
  <div class="footer-bottom">
    <span class="copy">Copyright 2018 &copy; Vaultmerrow. All Rights Reserved.</span>
    <span class="legal">Terms &amp; Conditions &nbsp;|&nbsp; Privacy Policy</span>
  </div>
</footer>

</body>
</html>
```